Redesign Of Current Landing Page

I need to redesign this landing page https://www.brightlanepromo.biz/?page=landing&landing=23 (Please do not opt in because when you do it will show you the home page. Please clear your cookies before going to this url above to view the 1 page landing page.)

Please use my updated website as a reference for colors and logo.
http://sitecradlewerk.com/dh/bpq/index.html

I would like the call to action to be a button that opens into a lead form...

Button would be "Download Samples"

Target Market(s)

small business owners

Industry/Entity Type

Marketing

Number of Pages Required

1 page

Colors

Designer to choose colors to be used in the design.

Requirements
Must have
• must be full responsive on all devices
Nice to have
• must have a legitimate professional apeal to it
Should not have
• open

```html
<!DOCTYPE html>
<html lang="en">
<head>
<meta charset="utf-8">
<title>BrightLane Promo Group – Incentives Landing</title>
<link href="https://fonts.googleapis.com/css2?family=Roboto:wght@400;500;700&display=swap" rel="stylesheet">
<style>
:root{
  --brand-blue:#0f74bd;
  --brand-blue-dark:#0b4f86;
  --button-gray:#8d8e92;
  --text-dark:#333;
  --text-muted:#777;
  --icon-gray:#7d7e82;
  --footer-gray:#8f9095;
  --white:#fff;
}
*{margin:0;padding:0;box-sizing:border-box}
html,body{width:914px;height:1200px;overflow:hidden;background:var(--white)}
body{position:relative;font-family:'Roboto',sans-serif;color:var(--text-dark)}
.abs{position:absolute}
.btn{position:absolute;background:var(--button-gray);color:var(--white);border-radius:5px;font-weight:500;display:flex;align-items:center;justify-content:center}
.btn-download{width:313px;height:33px;font-size:15px}

/* header */
.site-header{left:0;top:0;width:914px;height:68px}
.brand{left:92px;top:14px;display:flex;align-items:center;gap:6px}
.brand-mark{width:26px;height:26px;border-radius:50%;background:var(--brand-blue)}
.brand-name{font-size:22px;font-weight:700;color:var(--text-dark);letter-spacing:1px}
.call-icon{left:501px;top:14px}
.call-label{left:542px;top:13px;font-size:10px;color:var(--text-muted);font-weight:500}
.call-number{left:540px;top:25px;font-size:18px;font-weight:700;color:var(--brand-blue);letter-spacing:.3px}
.call-hours{left:542px;top:49px;font-size:9.5px;color:var(--text-muted)}
.btn-email{left:688px;top:19px;width:150px;height:33px;font-size:14.5px}

/* hero */
.hero{left:0;top:68px;width:914px;height:382px;overflow:hidden;background:var(--brand-blue)}
.hero-photo{position:absolute;left:230px;top:0;width:684px;height:382px;
  background:linear-gradient(90deg,rgba(15,116,189,1) 0%,rgba(120,150,175,.8) 25%,#cdbfb3 50%,#e8e2dc 75%,#f2efec 100%)}
.hero-title{left:100px;top:103px;font-size:27px;font-weight:700;color:var(--white)}
.hero-sub{left:100px;top:138px;font-size:19.5px;color:var(--white);line-height:24px;width:330px}
.hero-note{left:102px;top:188px;font-size:10.5px;color:var(--white);line-height:16px}
.hero .btn-download{left:100px;top:230px;width:313px}
.slider-btn{width:32px;height:32px;border-radius:50%;background:var(--brand-blue-dark);display:flex;align-items:center;justify-content:center}

/* imagine */
.tab-active{left:317px;top:461px;width:99px;height:45px;background:var(--brand-blue);color:var(--white);font-size:16.5px;font-weight:700;display:flex;align-items:center;justify-content:center}
.tab{left:438px;top:473px;font-size:16.5px;font-weight:700;color:var(--brand-blue)}
.imagine-panel{left:75px;top:506px;width:763px;height:174px;background:var(--brand-blue);color:var(--white);text-align:center;font-size:9px;line-height:11px;padding:22px 50px 0}
.imagine-panel p{margin-bottom:10px}
.imagine-panel .btn-download{left:225px;top:115px}

/* reasons */
.section-title{left:0;width:914px;text-align:center;font-size:17px;font-weight:700;color:var(--brand-blue)}
.reason{top:748px;width:120px;text-align:center}
.reason svg{display:block;margin:0 auto 18px}
.reason p{font-size:8.5px;line-height:12px;color:var(--text-dark)}

/* testimonial */
.quote-badge{left:437px;top:957px;width:40px;height:40px;border-radius:50%;background:var(--button-gray);display:flex;align-items:center;justify-content:center}
.testimonial-text{left:148px;top:1004px;width:618px;text-align:center;font-size:9.2px;line-height:19.6px;color:#555}
.author{left:0;width:914px;text-align:center;font-size:12px;font-weight:700}
.author-name{top:1101px;color:var(--brand-blue)}
.author-place{top:1121px;color:var(--text-muted)}

.site-footer{left:0;top:1158px;width:914px;height:42px;background:var(--footer-gray);color:var(--white);font-size:10px;display:flex;align-items:center;justify-content:center}
</style>
</head>
<body>

<header class="abs site-header">
  <div class="abs brand"><span class="brand-mark"></span><span class="brand-name">BLPG</span></div>
  <svg class="abs call-icon" width="30" height="30" viewBox="0 0 30 30">
    <circle cx="15" cy="15" r="15" fill="#0f74bd"/>
    <path d="M10.5 8.5c.8-.6 1.6-.4 2 .3l1.3 2.3c.4.7.2 1.4-.4 1.8l-.9.6c.6 1.5 1.8 2.9 3.3 3.7l.7-.8c.5-.6 1.3-.7 1.9-.3l2.2 1.4c.7.4.8 1.3.2 1.9l-1 1.1c-.9.9-2.4 1-3.6.4-3.2-1.6-5.5-4.2-6.7-7.6-.4-1.3-.1-2.6.9-3.4z" fill="#fff"/>
  </svg>
  <div class="abs call-label">Call Us</div>
  <div class="abs call-number">1-800-555-0147</div>
  <div class="abs call-hours">Mon-Fri 8am-5pm PST</div>
  <div class="btn btn-email">Email Us Samples</div>
</header>

<section class="abs hero">
  <div class="hero-photo" role="img" aria-label="Photo of three colleagues reviewing documents together at a desk"></div>
  <h1 class="abs hero-title">Attract more customers</h1>
  <p class="abs hero-sub">who spend more money with your business more often!</p>
  <p class="abs hero-note">Using Free Vacation &amp; Cruise Certificates And Other Incentives<br>Without Breaking The Bank!</p>
  <div class="btn btn-download">Download Free Samples Of Our Incentives</div>
  <div class="abs slider-btn" style="left:102px;top:290px"><svg width="10" height="12" viewBox="0 0 10 12"><path d="M7 1 2 6l5 5" stroke="#fff" stroke-width="2" fill="none"/></svg></div>
  <div class="abs slider-btn" style="left:142px;top:290px"><svg width="10" height="12" viewBox="0 0 10 12"><path d="M3 1l5 5-5 5" stroke="#fff" stroke-width="2" fill="none"/></svg></div>
</section>

<div class="abs tab-active">IMAGINE</div>
<div class="abs tab">HOW CAN WE DO IT?</div>
<section class="abs imagine-panel">
  <p>Being able to create exciting give away promotions that will boost your sales without ever having to worry about cost.</p>
  <p>BrightLane Promo Group, Inc. provides high-perceived value promotional incentives to businesses that want to advertise an exciting Give Away that will instantly attract more customers from your existing advertising efforts.</p>
  <p>Your business can give away incentive certificates that are redeemable for luxury hotel &amp; resort stays with airfare included, cruises, cash for gas, groceries, dining and even electronic goods.</p>
  <div class="btn btn-download">Download Free Samples Of Our Incentives</div>
</section>

<h2 class="abs section-title" style="top:699px">WHY OFFER INCENTIVES TO CUSTOMERS?</h2>

<div class="abs reason" style="left:75px">
  <svg width="34" height="30" viewBox="0 0 34 30" fill="#7d7e82"><rect x="1" y="25" width="4" height="4"/><rect x="8" y="21" width="5" height="8"/><rect x="16" y="15" width="5" height="14"/><rect x="24" y="9" width="5" height="20"/><rect x="31" y="2" width="3" height="27"/></svg>
  <p>Increase Responses From Your Existing Ads</p>
</div>
<div class="abs reason" style="left:202px">
  <svg width="30" height="30" viewBox="0 0 30 30"><path d="M27 6l-5 5-3-1-1-3 5-5c-4-1-8 2-8 6 0 1 0 2 .5 2.5L3 23a2.5 2.5 0 0 0 4 4l12.5-12.5c.5.5 1.5.5 2.5.5 4 0 7-4 6-8z" fill="#7d7e82"/></svg>
  <p>#1.Sales Closing Tool - Gift w/ Purchase</p>
</div>
<div class="abs reason" style="left:329px">
  <svg width="30" height="30" viewBox="0 0 30 30"><path d="M15 1l4.3 9 9.7 1.2-7.1 6.7 1.8 9.6L15 22.8l-8.7 4.7 1.8-9.6L1 11.2 10.7 10z" fill="#7d7e82"/></svg>
  <p>Build Brand Awareness and Trust</p>
</div>
<div class="abs reason" style="left:456px">
  <svg width="36" height="30" viewBox="0 0 36 30" fill="#7d7e82"><circle cx="9" cy="6" r="4.5"/><circle cx="27" cy="6" r="4.5"/><circle cx="18" cy="10" r="5.5"/><path d="M1 22c0-6 3-9 8-9 2 0 3 .5 4 1-3 2-4 5-4 8z"/><path d="M35 22c0-6-3-9-8-9-2 0-3 .5-4 1 3 2 4 5 4 8z"/><path d="M8 29c0-8 4-12 10-12s10 4 10 12z"/></svg>
  <p>Insure The Sale Over Your Competition</p>
</div>
<div class="abs reason" style="left:583px">
  <svg width="34" height="30" viewBox="0 0 34 30" fill="#7d7e82"><path d="M2 9h22V4l9 7-9 7v-5H2z"/><path d="M32 19H10v-5l-9 7 9 7v-5h22z"/></svg>
  <p>Boost Repeat and Referral Business-</p>
</div>
<div class="abs reason" style="left:711px">
  <svg width="34" height="30" viewBox="0 0 34 30"><rect x="1.5" y="5.5" width="31" height="19" fill="none" stroke="#7d7e82" stroke-width="3"/><path d="M3 7h5a5 5 0 0 1-5 5zM31 7h-5a5 5 0 0 0 5 5zM3 23h5a5 5 0 0 0-5-5zM31 23h-5a5 5 0 0 1 5-5z" fill="#7d7e82"/><circle cx="17" cy="15" r="6" fill="none" stroke="#7d7e82" stroke-width="2"/><path d="M16 12h1.5v6" stroke="#7d7e82" stroke-width="1.8" fill="none"/></svg>
  <p>Improve Retention Rates</p>
</div>

<div class="btn btn-download" style="left:300px;top:869px">Download Free Samples Of Our Incentives</div>

<h2 class="abs section-title" style="top:932px">TESTIMONIALS</h2>
<div class="abs quote-badge">
  <svg width="20" height="16" viewBox="0 0 20 16" fill="#fff"><path d="M1 8h6v7H1zM1 8c0-4 2-7 6-7v3c-2 0-3 2-3 4z"/><path d="M11 8h6v7h-6zM11 8c0-4 2-7 6-7v3c-2 0-3 2-3 4z"/></svg>
</div>
<svg class="abs" style="left:111px;top:1023px" width="10" height="14" viewBox="0 0 10 14"><path d="M8 1 2 7l6 6" stroke="#999" stroke-width="1.6" fill="none"/></svg>
<svg class="abs" style="left:795px;top:1023px" width="10" height="14" viewBox="0 0 10 14"><path d="M2 1l6 6-6 6" stroke="#999" stroke-width="1.6" fill="none"/></svg>
<p class="abs testimonial-text">I began using your incentives two years ago to boost lead generation efforts. I have experienced a 63% increase in lead captures. And, even more importantly, my sales have increased as well. The ability to offer unlimited certificates and not having to pay for each certificate I give away is perhaps the best feature of the program, but having the flexibility to email or print certificates for my customers is also wonderful. I even use your html banners to automate my promotions right on my website!,</p>
<div class="abs author author-name">Mark D.</div>
<div class="abs author author-place">Fairview, TN</div>

<footer class="abs site-footer">© 2017 BrightLane Promo Group, Inc. - All Rights Reserved</footer>

</body>
</html>
```